Business Card Design Project

This is the first time we use our new logo. We need a business card that we can use both on our institutional corporate relationships and also that works for our staff that deals with consumers directly.

VELUNDA is a new company dedicated to empower consumers and to provide them with the best choices for specialized health care using the latest telemedicine technology (medicine at a distance via videoconference).

We want to print this cards in high quality materials and process. We will like designs that allow us to use UV spot varnish and other techniques that will differentiate us.

We are including Two different versions of Color logos. In addition we are including white over black background logos. Those can be used replacing the black for a color.

Please note this is the first time we will be creating any corporate materials with our new logo and colors.

Target Market(s)

34+ consumers of medium high and high socioeconomic levels.

Industry/Entity Type

Health

Requirements
Must have
• Our logo on its original colors
Should not have
• Any other graphical element or design that is not our logo

```html
<!DOCTYPE html>
<html lang="en">
<head>
<meta charset="utf-8">
<title>VELUNDA — Business Card</title>
<link href="https://fonts.googleapis.com/css2?family=Jost:wght@400;500;600&display=swap" rel="stylesheet">
<style>
  :root {
    --page-bg: #ececec;
    --card-blue: #2474bf;
    --card-blue-light: rgba(110, 175, 228, 0.55);
    --card-blue-deep: rgba(20, 90, 160, 0.35);
    --card-white: #ffffff;
    --ink-navy: #1d4f7a;
    --mark-blue: #5aaee0;
    --band-blue: #2272bd;
  }
  * { margin: 0; padding: 0; box-sizing: border-box; }
  html, body {
    width: 1113px;
    height: 1200px;
    overflow: hidden;
    background: var(--page-bg);
    font-family: "Jost", "Futura", sans-serif;
  }
  .canvas {
    position: relative;
    width: 1113px;
    height: 1200px;
  }
  .card {
    position: absolute;
    left: 117px;
    width: 876px;
    height: 497px;
    overflow: hidden;
  }
  /* Front side */
  .card--front {
    top: 80px;
    background: var(--card-blue);
  }
  .front-decoration {
    position: absolute;
    inset: 0;
    background:
      radial-gradient(ellipse 270px 250px at 610px 250px, var(--card-blue-light) 0%, rgba(110, 175, 228, 0.2) 55%, rgba(36, 116, 191, 0) 100%),
      radial-gradient(ellipse 330px 300px at 640px 260px, var(--card-blue-deep) 0%, rgba(36, 116, 191, 0) 100%);
  }
  /* Back side */
  .card--back {
    top: 623px;
    background: var(--card-white);
  }
  .brand-dot {
    position: absolute;
    left: 178px;
    top: 118px;
    width: 112px;
    height: 112px;
    border-radius: 50%;
    background: var(--mark-blue);
  }
  .brand {
    position: absolute;
    left: 60px;
    top: 292px;
    width: 350px;
    text-align: center;
    font-weight: 600;
    font-size: 66px;
    line-height: 1;
    letter-spacing: 4px;
    color: var(--ink-navy);
  }
  .divider {
    position: absolute;
    left: 447px;
    top: 61px;
    width: 2px;
    height: 335px;
    background: var(--ink-navy);
  }
  .contact {
    position: absolute;
    left: 511px;
    top: 66px;
    color: var(--ink-navy);
  }
  .contact__name {
    font-size: 36px;
    font-weight: 600;
    line-height: 1.1;
  }
  .contact__role {
    font-size: 21px;
    font-weight: 400;
    margin-top: 2px;
  }
  .contact__lines {
    font-size: 23px;
    font-weight: 400;
    line-height: 35px;
  }
  .contact__lines--reach { margin-top: 34px; }
  .contact__lines--address { margin-top: 16px; }
  .bottom-band {
    position: absolute;
    left: 0;
    bottom: 0;
    width: 876px;
    height: 50px;
  }
</style>
</head>
<body>
  <main class="canvas">
    <section class="card card--front" aria-label="Card front">
      <div class="front-decoration" role="img" aria-label="Large faint brand symbol decoration in light blue tones"></div>
    </section>

    <section class="card card--back" aria-label="Card back">
      <div class="brand-dot" aria-hidden="true"></div>
      <div class="brand">VELUNDA</div>
      <div class="divider"></div>
      <div class="contact">
        <div class="contact__name">Name Surname</div>
        <div class="contact__role">manager</div>
        <div class="contact__lines contact__lines--reach">
          <div>555.204.3381</div>
          <div>jmoran@velundahealth.com</div>
          <div>www.velundahealth.com</div>
        </div>
        <div class="contact__lines contact__lines--address">
          <div>Your Address Goes Here</div>
          <div>Another Row</div>
          <div>City, State, Zipcode</div>
        </div>
      </div>
      <svg class="bottom-band" viewBox="0 0 876 50" preserveAspectRatio="none" aria-hidden="true">
        <path d="M0 28 Q438 -8 876 28 L876 50 L0 50 Z" fill="var(--band-blue)"/>
      </svg>
    </section>
  </main>
</body>
</html>
```